Website for a financial survey consultancy

WHO WE ARE
We're a niche HR consultancy specialising in salary comparison surveys for the financial asset management industry. We position ourselves as a small, highly responsive organisation with a strong personal relationship with each of our 50+ blue-chip clients.

WHAT WE DO
Our business is 80% surveys (= products), 20% consultancy (= services). The surveys are a set of online products which clients interact with to find the information they are interested in.

WHAT WE WANT
We are completely revising our existing marketing website and need a new up-to-date look and feel for the site. We want you to design 2 web pages
- Home page
- Internal content page

More details below in Must Have Priorities.

REFERENCE SITES
- www.veltramoor.com - nice background image
- www.plimweather.com - ignoring the animations
- www.gasketvale.com
- www.quorbin.com - clean, fresh, styly but prob not corporate enough
- www.dulveropinex.com - spacious, beautiful, slightly dated tho
- www.tambly.co.uk - ignore the colours. Like the simplicity, larger font size (although want to stick with sans-serif fonts for main content)

DELIVERABLES
The final designs should be delivered as one or more PSD files with clearly named layers. All design elements and treatments should be separated out, for example use adjustment layers rather than applied (and subsequently irreversible) adjustments, strokes, shading, etc.

WHAT NEXT
I'll be monitoring the contest every day and can respond to questions fast. You can IM me on Chatterlyne or QBX.

Reason: Hi folks,

I am extending the deadline to this project as I am travelling this week and therefore will not be able to make a final decision until next Monday. I will try and provide further feedback over the course of this week but I am only going to be online occasionally so be prepared to wait a few days for a reply from me.

Thanks for all the designs so far.

Tobias

Target Market(s)

In order of importance, most important first

1. Potential customers - UK & US financial industry HR professionals, short on time. Heard about us already, want to find out more about what we do, confirm relevance for their needs. Core goal - establish credibility: are we properly resourced, will we be around for years to come, are we *real*.

2. Existing customers - UK & US financial industry professionals, short on time, under pressure, want results quickly, minimum faff, expect high quality, slickly presented information. Primary action: login and use surveys.

3. Industry professionals/researchers - probably arriving through blog content, looking to browse and hoover information. Valuable for their ability to spread awareness of who we are amongst their peers.

Industry/Entity Type

Financial

Requirements
Must have
• GENERAL
Style cues - Corporate, professional, financial, stylish, slick, clean, spacious, light
Size - standard 960px grid

NAVIGATION
- [ Home | About us | Surveys | Consulting | Blog ]
- Sub-nav (roll-over dropdown) on About Us, Surveys & Consulting

ALL PAGES
- Site navigation
- Client login (on screen permanently or link to ajaxy in-page pop-up)
- Footer section
- Existing logo (attached)* - this is obviously an important reference point in the design, esp colour

HOME PAGE
- Communicate (link thru to?) survey/consulting split
- Large photo(s)/backdrop (2-3 interchangeable options ideally). Please consider what rights agreement will be necessary for any photos you include in your design.
- Possibly bigger more prominent version of logo
- Strap line/sentence - "Focussed data is the key to success"
- 3 recent blog posts (should look good with and without blog post images)
- Free downloadable PDF research report + supporting blurb

INTERNAL PAGE
- Page title
- Content - typical page will be less than one screenfull
- Level 1 sub-heading
- Level 2 sub-heading
- Bulleted list
- Content supporting image (any image will do - interested in placement, borders (if any), spacing, caption, etc)
- 'Do something' button

* Note: there is some internal debate about this logo at the moment. Some (me) are keen for it to change, some (not me!) are not. If you have an web page design idea/concept that requires an evolution of the logo, go ahead and evolve it. We can explore this further in the design process as necessary, but don't sweat it.
Nice to have
• Values to communicate
- Knowledgeable
- Professional
- Secure
- Personal
- Experienced
- Financial industry specific
- Accurate
- Reliable
Should not have
• - Search box
- Social media links, other than RSS feed button (discrete)

```html
<!DOCTYPE html>
<html lang="en">
<head>
<meta charset="utf-8">
<title>HR Consultancy – Calvane</title>
<link rel="stylesheet" href="https://fonts.googleapis.com/css2?family=Open+Sans:wght@400;600;700&family=Noto+Sans:wght@400;700&display=swap">
<style>
  :root {
    --brand-red: #8a1515;
    --brand-red-dark: #6a0a0a;
    --brand-red-light: #a32222;
    --accent-rose: #b94a4a;
    --ink: #111111;
    --body-text: #1a1a1a;
    --page-bg: #f4f5f7;
    --panel-bg: #ffffff;
    --rule: #b9b9b9;
    --city-haze: #e4e9ef;
    --city-steel: #b4c1d0;
    --city-glass: #8ea4c0;
    --city-shadow: #5f7491;
  }
  * { box-sizing: border-box; margin: 0; padding: 0; }
  html, body { width: 1200px; height: 664px; overflow: hidden; }
  body {
    position: relative;
    background: var(--page-bg);
    font-family: Verdana, "Noto Sans", sans-serif;
    color: var(--body-text);
  }
  .top-bar, .site-footer {
    position: absolute; left: 0; width: 1200px;
    background: linear-gradient(var(--brand-red-light), var(--brand-red-dark));
  }
  .top-bar { top: 0; height: 19px; }
  .main-nav {
    position: absolute; right: 185px; top: 2px;
    display: flex; font-family: "Open Sans", sans-serif; font-weight: 600; font-size: 10px;
  }
  .main-nav a, .footer-links a { color: #fff; text-decoration: none; }
  .main-nav a + a::before, .footer-links a + a::before {
    content: "|"; color: #e7b8b8; margin: 0 7px; font-weight: 400;
  }
  .city-backdrop {
    position: absolute; left: 60px; top: 30px; width: 1000px; height: 612px;
    background:
      radial-gradient(ellipse 22% 48% at 70% 52%, var(--city-shadow) 0%, rgba(95,116,145,0) 100%),
      radial-gradient(ellipse 20% 40% at 40% 58%, var(--city-glass) 0%, rgba(142,164,192,0) 100%),
      radial-gradient(ellipse 14% 34% at 92% 50%, var(--city-glass) 0%, rgba(142,164,192,0) 100%),
      radial-gradient(ellipse 14% 26% at 16% 70%, var(--city-steel) 0%, rgba(180,193,208,0) 100%),
      radial-gradient(ellipse 52% 50% at 52% 60%, var(--city-steel) 0%, var(--city-haze) 62%, rgba(244,245,247,0) 100%);
  }
  .brand-block {
    position: absolute; left: 183px; top: 19px; width: 107px; height: 103px;
    background: var(--brand-red-dark);
  }
  .brand-name {
    position: absolute; left: 183px; top: 128px; width: 107px;
    font-family: "Open Sans", sans-serif; font-weight: 600; font-size: 24px;
    color: var(--brand-red-dark); text-align: center;
  }
  .hero-title {
    position: absolute; left: 311px; top: 28px;
    font-family: "Open Sans", sans-serif; font-weight: 700; font-size: 39px; line-height: 50px;
    color: var(--ink); letter-spacing: -.5px;
  }
  .hero-strap {
    position: absolute; left: 313px; top: 76px;
    font-family: "Open Sans", sans-serif; font-weight: 600; font-size: 19px;
    color: var(--accent-rose);
  }
  .panel {
    position: absolute; background: var(--panel-bg);
    box-shadow: 0 1px 3px rgba(0,0,0,.25);
  }
  .panel-heading {
    height: 24px; padding: 3px 6px;
    background: linear-gradient(var(--brand-red-light), var(--brand-red-dark));
    color: #fff; font-family: "Open Sans", sans-serif; font-weight: 700; font-size: 13.5px;
  }
  .feature { left: 183px; width: 310px; height: 99px; background: linear-gradient(#fff, #ececec); }
  .feature--surveys { top: 373px; }
  .feature--consulting { top: 489px; }
  .feature-body { display: flex; padding: 5px 4px; gap: 6px; }
  .feature-photo { width: 99px; height: 64px; border: 1px solid #333; flex: none; }
  .feature-photo--surveys { background: linear-gradient(135deg, #e8eef6, #9fb3cc); }
  .feature-photo--consulting { background: linear-gradient(135deg, #9ab07a, #4a4f55); }
  .feature-text { font-size: 9px; line-height: 11.3px; padding-top: 2px; }
  .read-more {
    display: inline-block; margin-top: 10px; color: var(--brand-red);
    font-weight: 700; font-size: 9.5px; text-decoration: none; letter-spacing: .3px;
  }
  .read-more svg { margin-right: 4px; vertical-align: middle; }
  .blog { left: 807px; top: 258px; width: 204px; height: 277px; }
  .blog-list { padding: 7px 11px 0 8px; list-style: none; }
  .blog-post { border-bottom: 1px dotted var(--rule); height: 80px; padding-top: 2px; }
  .blog-post h3 { font-size: 9px; font-weight: 700; letter-spacing: .3px; line-height: 12px; margin-bottom: 1px; }
  .blog-post p { font-size: 9px; line-height: 11.3px; }
  .blog-post .read-more { display: block; text-align: right; margin: 2px 4px 0 0; }
  .report {
    left: 807px; top: 551px; width: 204px; height: 46px;
    display: flex; align-items: center; padding: 0 5px; gap: 6px;
  }
  .report-blurb {
    font-family: "Open Sans", sans-serif; font-weight: 600; font-size: 10.5px; line-height: 13px; color: var(--ink);
  }
  .report-button {
    margin-left: auto; width: 59px; height: 31px; border-radius: 15px;
    background: linear-gradient(var(--brand-red-light), var(--brand-red-dark));
    border: 1px solid #5a0a0a; box-shadow: inset 0 0 0 2px #e8c6c6;
    color: #fff; font-family: "Open Sans", sans-serif; font-weight: 600; font-size: 9.5px;
    line-height: 11px; text-align: center; padding-top: 4px; text-decoration: none;
  }
  .site-footer { top: 642px; height: 22px; font-size: 9.5px; color: #fff; letter-spacing: .3px; }
  .copyright { position: absolute; left: 185px; top: 5px; }
  .footer-links { position: absolute; right: 185px; top: 5px; }
</style>
</head>
<body>
  <header class="top-bar">
    <nav class="main-nav">
      <a href="#">Home</a><a href="#">About Us</a><a href="#">Services</a><a href="#">Consulting</a><a href="#">Blog</a><a href="#">Contact Us</a>
    </nav>
  </header>

  <div class="city-backdrop" role="img" aria-label="Backdrop of modern glass office towers in a business district"></div>

  <div class="brand-block"></div>
  <div class="brand-name">Calvane</div>

  <h1 class="hero-title">HR Consultancy</h1>
  <p class="hero-strap">Focused Data is the Key to Success:</p>

  <section class="panel feature feature--surveys">
    <h2 class="panel-heading">Surveys:</h2>
    <div class="feature-body">
      <div class="feature-photo feature-photo--surveys" role="img" aria-label="Pen ticking boxes on a survey form"></div>
      <div class="feature-text">
        <p>Lorem Ipsum is simply dummy text of the printing and typesetting industry. Lorem Ipsum has been the industry's</p>
        <a class="read-more" href="#"><svg width="6" height="6" viewBox="0 0 6 6"><path d="M0 3h5M3 1l2 2-2 2" stroke="#8a1515" fill="none"/></svg>Read More</a>
      </div>
    </div>
  </section>

  <section class="panel feature feature--consulting">
    <h2 class="panel-heading">Consulting:</h2>
    <div class="feature-body">
      <div class="feature-photo feature-photo--consulting" role="img" aria-label="Business people meeting at a table"></div>
      <div class="feature-text">
        <p>Lorem Ipsum is simply dummy text of the printing and typesetting industry. Lorem Ipsum has been the industry's</p>
        <a class="read-more" href="#"><svg width="6" height="6" viewBox="0 0 6 6"><path d="M0 3h5M3 1l2 2-2 2" stroke="#8a1515" fill="none"/></svg>Read More</a>
      </div>
    </div>
  </section>

  <aside class="panel blog">
    <h2 class="panel-heading">Latest Blog Posts:</h2>
    <ul class="blog-list">
      <li class="blog-post"><h3>Topic by John. M:</h3><p>Lorem Ipsum is simply dummy text of the printing and typesetting industry. Lorem Ipsum has been the industry's standard.</p><a class="read-more" href="#">Read More</a></li>
      <li class="blog-post"><h3>Topic by John. M:</h3><p>Lorem Ipsum is simply dummy text of the printing and typesetting industry. Lorem Ipsum has been the industry's standard.</p><a class="read-more" href="#">Read More</a></li>
      <li class="blog-post"><h3>Topic by John. M:</h3><p>Lorem Ipsum is simply dummy text of the printing and typesetting industry. Lorem Ipsum has been the industry's standard.</p><a class="read-more" href="#">Read More</a></li>
    </ul>
  </aside>

  <aside class="panel report">
    <svg width="32" height="34" viewBox="0 0 32 34" aria-hidden="true">
      <path d="M4 1h18l7 7v25H4z" fill="#c62020"/>
      <path d="M22 1v7h7" fill="#8a1010"/>
      <text x="7" y="14" font-family="Open Sans, sans-serif" font-size="8" font-weight="700" fill="#fff">PDF</text>
    </svg>
    <p class="report-blurb">Research Report<br>Supporting Blurb</p>
    <a class="report-button" href="#">Download<br>pdf file</a>
  </aside>

  <footer class="site-footer">
    <span class="copyright">Copyright © 2011 Calvane | All Rights Reserved</span>
    <nav class="footer-links"><a href="#">Legal</a><a href="#">Sitemap</a><a href="#">Contact Us</a></nav>
  </footer>
</body>
</html>
```